Wedding Invitations

We are a printing company "inkhollow" and require multiple wedding invitation designs for our customers in store and online. We would like the designs to be editable in Photoshop if possible, if not then a layout with suggested fonts would be the next best option. We are open to suggestions on design but would like to stick to the general wedding themes some with a modern and some with a classical feel

Industry/Entity Type

Printing

```html
<!DOCTYPE html>
<html lang="en">
<head>
<meta charset="UTF-8">
<title>Wedding Invitation – City Skyline</title>
<link rel="stylesheet" href="https://fonts.googleapis.com/css2?family=Great+Vibes&family=Roboto+Slab:wght@300&display=swap">
<style>
  :root {
    --sky: #ffffff;
    --charcoal: #454545;
    --teal: #1fa79b;
    --soft-grey: #b9b9b9;
    --serif: "Roboto Slab", Georgia, serif;
    --script: "Great Vibes", cursive;
  }
  html, body {
    margin: 0;
    padding: 0;
    width: 1200px;
    height: 857px;
    overflow: hidden;
    background: var(--charcoal);
  }
  .invitation {
    position: relative;
    width: 1200px;
    height: 857px;
    background: var(--charcoal);
    overflow: hidden;
    font-family: var(--serif);
    font-weight: 300;
    color: var(--soft-grey);
  }
  .skyline {
    position: absolute;
    top: 0;
    left: 0;
    width: 1200px;
    height: 220px;
    display: block;
  }
  .request {
    position: absolute;
    right: 25px;
    top: 246px;
    margin: 0;
    text-align: right;
    font-size: 27px;
    line-height: 38px;
  }
  .couple {
    position: absolute;
    margin: 0;
    font-family: var(--script);
    font-weight: 400;
    font-size: 112px;
    line-height: 112px;
    height: 112px;
    color: var(--teal);
    white-space: nowrap;
    transform-origin: 0 100%;
  }
  .couple--bride { left: 58px; top: 512px; transform: rotate(-21deg); }
  .couple--groom { left: 132px; top: 632px; transform: rotate(-19deg); }
  .date-time {
    position: absolute;
    right: 25px;
    top: 560px;
    margin: 0;
    text-align: right;
    font-size: 29px;
    line-height: 40px;
  }
  .venue {
    position: absolute;
    right: 25px;
    top: 690px;
    margin: 0;
    text-align: right;
    font-style: normal;
    font-size: 18px;
    line-height: 30px;
  }
  .reception {
    position: absolute;
    right: 25px;
    top: 780px;
    margin: 0;
    font-size: 18px;
    line-height: 24px;
  }
</style>
</head>
<body>
<main class="invitation">
  <svg class="skyline" viewBox="0 0 1200 220" role="img" aria-label="City skyline silhouette with domed cathedral and towers against a white sky" preserveAspectRatio="none">
    <defs>
      <linearGradient id="sky-to-city" x1="0" y1="0" x2="0" y2="1">
        <stop offset="0" stop-color="#ffffff"/>
        <stop offset="0.35" stop-color="#f2f2f2"/>
        <stop offset="1" stop-color="#454545"/>
      </linearGradient>
    </defs>
    <rect width="1200" height="220" fill="url(#sky-to-city)"/>
  </svg>

  <p class="request">Mr &amp; Mrs Whitfield Request the pleasure of your<br>company at the marriage of their daugther</p>

  <h1 class="couple couple--bride">Clara Whitfield &amp;</h1>
  <h1 class="couple couple--groom">Oliver Marsden</h1>

  <p class="date-time">Saturday Tenth Novemeber 2013<br>Starting at Two o’clock in the afternoon</p>

  <address class="venue">Aldric Church, Mill Row,<br>Ashbury, England<br>AB3 7QT</address>

  <p class="reception">Reception to follow with Dinner and Dancing</p>
</main>
</body>
</html>
```